Belvascotravel.com web design project + logo design

Hi,

We are a Russian online tour operator - sunkettle.com

We are looking to tranmsfer our domain to belvascotravel.com. The website and logo need to be belvascoesque - we are not looking to change our functionality, but we need to make the website much more attracitve to clients, much more wild looking but at the same time remaining a professional travel company.

The main concept of the website should be innovative travel (as belvasco was an innovator). Alternatively, you could go down the artist route and go down the draw / design your own tour road.

On our website the customer is able to combine travel services (hotels, flights, Visa services, and soon chauffeur, car rental etc...) put it into their basket (the basket definitely has to look better than it is at the moment) and pay for it in one go by card.

We are also stressin our customer support with web chat, call centre etc... (call centre number at the top of the page)

We aim to provide an easy user experience, but we need to make it have some more style, so I will be waiting for what you guys can come up with.
Let me know if you have any questions - skype is: mrdolbarin

Industry/Entity Type

It Company

Requirements
Must have
• It is quite a simple task - to take the existing website sunkettle.com and belvascosize it to create belvascotravel.com, the functionality of the website will remain the same and there are not many pages in the website. Homepage, Checkout step1, Checkout step 2 (you can view both of these if you select a service) and the generic pages for T&C''s, Privacy policy etc...

IMPORTANT UPDATE

We are also looking at how the search results will look in the designs, (please do a search on our website for hotel / flight)

```html
<!DOCTYPE html>
<html lang="en">
<head>
<meta charset="utf-8">
<title>Belvascotravel.com</title>
<link href="https://fonts.googleapis.com/css2?family=Open+Sans:wght@400;600;700&family=Signika:wght@300;400;600&display=swap" rel="stylesheet">
<style>
:root{
  --sky-top:#1d56b8;
  --sky-mid:#3f7fd0;
  --sky-low:#6d9bc4;
  --water:#2c5f8f;
  --lime:#cdd84f;
  --lime-dark:#a9b534;
  --maroon:#4d2324;
  --maroon-tail:#7a3436;
  --footer:#5a2b2c;
  --ink:#333;
  --grey-text:#8a8a8a;
  --panel:rgba(70,120,190,.72);
  --tab-bg:#f0f0f0;
  --link:#1a8ad0;
  --phone:#3f6c96;
  --page-bg:#f4f4f4;
}
*{box-sizing:border-box;margin:0;padding:0}
html,body{width:1015px;height:1200px;overflow:hidden}
body{position:relative;background:var(--page-bg);font-family:"Open Sans",sans-serif;color:var(--ink)}
.hero{position:absolute;left:0;top:0;width:1015px;height:520px;
  background:linear-gradient(180deg,var(--sky-top) 0%,var(--sky-mid) 35%,var(--sky-low) 62%,var(--water) 78%,#1f4a70 100%)}
.header{position:absolute;left:118px;top:0;width:779px;height:85px;background:#fff}
.brand{position:absolute;left:22px;top:30px;display:flex;align-items:center;gap:7px}
.brand-dot{width:18px;height:18px;border-radius:50%;background:#6aa62e}
.brand-name{font-family:"Signika",sans-serif;font-weight:600;font-size:17px;color:#4a3a2c}
.nav a{position:absolute;top:0;height:85px;line-height:94px;font-size:9.5px;font-weight:700;color:#333;text-decoration:none;white-space:nowrap}
.nav a.active{left:287px;width:61px;background:var(--lime);color:#fff;text-align:center}
.search{position:absolute;left:433px;top:111px;width:448px;height:286px;background:var(--panel);border:1px solid rgba(255,255,255,.35)}
.search-tabs{display:flex;height:43px;border-bottom:1px solid rgba(255,255,255,.25);background:rgba(40,90,160,.35)}
.search-tabs span{display:block;padding:0 22px;line-height:43px;font-family:"Signika",sans-serif;font-size:13px;color:#fff}
.search-tabs span.on{background:rgba(90,140,210,.6);width:104px;text-align:center;padding:0}
.row{position:absolute;display:flex;align-items:center}
.lbl{font-size:11px;font-weight:700;color:#fff;text-align:right;white-space:nowrap;text-shadow:0 1px 1px rgba(0,0,0,.3)}
.fld{height:24px;background:#fff;border:1px solid #ddd;font-size:9px;color:#aaa;line-height:22px;padding-left:9px;white-space:nowrap}
.checks{position:absolute;left:278px;top:173px;display:flex;gap:14px;font-size:9px;color:#fff;white-space:nowrap}
.checks i{display:inline-block;width:9px;height:9px;background:#fff;margin-right:4px;vertical-align:-1px;font-style:normal;font-size:8px;line-height:9px;color:#333;text-align:center}
.btn-check{position:absolute;left:124px;top:241px;width:198px;height:24px;background:var(--lime);color:#3a3a3a;font-size:11px;font-weight:700;text-align:center;line-height:24px}
.services{position:absolute;left:118px;top:397px;width:779px;height:123px;background:#fff;border-radius:3px 3px 0 0}
.svc{position:absolute;top:20px;width:180px}
.svc h3{display:flex;align-items:center;gap:8px;font-family:"Signika",sans-serif;font-weight:300;font-size:14px;color:#2d2d2d;white-space:nowrap}
.svc p{margin-top:9px;font-size:10px;line-height:14px;color:var(--grey-text)}
.svc .more{display:inline-block;margin-top:10px;padding:0 7px;height:20px;line-height:20px;background:var(--lime);border:1px solid var(--lime-dark);border-radius:2px;font-size:9.5px;font-style:italic;color:#3a3a3a}
.banner{position:absolute;left:118px;top:528px;width:779px;height:53px;background:var(--maroon)}
.tail{position:absolute;top:535px}
.banner h2{position:absolute;left:52px;top:7px;font-family:"Signika",sans-serif;font-weight:300;font-size:17px;color:#fff}
.banner p{position:absolute;left:53px;top:32px;font-size:10px;color:#fff;white-space:nowrap}
.banner .slash{position:absolute;left:24px;top:10px}
.btn-contact{position:absolute;left:605px;top:14px;width:129px;height:28px;background:#fff;border:1px solid #ccc;font-family:"Signika",sans-serif;font-size:13px;line-height:26px;text-align:center;color:#333}
.content{position:absolute;left:118px;top:581px;width:779px;height:529px;background:#fff;border:1px solid #e2e2e2;border-top:none}
.tabs{position:absolute;left:0;top:9px;width:777px;height:45px;background:var(--tab-bg);border-bottom:1px solid #e2e2e2}
.tabs span{position:absolute;top:0;line-height:45px;font-family:"Signika",sans-serif;font-weight:300;font-size:13px;color:#333;white-space:nowrap}
.tabs .on{left:1px;width:155px;height:46px;background:#fff;text-align:center;font-size:17px;font-weight:300;color:#555;border-top:1px solid #e2e2e2;border-left:1px solid #e2e2e2}
.tabs .phone{right:15px;top:8px;line-height:14px;text-align:center;font-size:11px;color:var(--phone)}
.intro{position:absolute;left:16px;top:78px;width:745px;font-size:10px;line-height:19px;color:#777}
.col{position:absolute;top:193px;width:350px}
.col h4{display:flex;align-items:center;gap:12px;font-family:"Signika",sans-serif;font-weight:300;font-size:13px;color:#555;white-space:nowrap}
.col ul{list-style:none;margin-top:26px}
.col li{position:relative;padding-left:24px;font-size:10px;line-height:18px;color:#888;height:63.5px}
.col li::before{content:"";position:absolute;left:0;top:7px;width:4px;height:4px;border-radius:50%;background:#333}
.more-link{position:absolute;left:19px;top:499px;font-family:"Signika",sans-serif;font-size:12.5px;color:var(--link)}
.footer{position:absolute;left:0;top:1152px;width:1015px;height:48px;background:var(--footer);border-top:2px solid #6e3a3b}
.footer .copy{position:absolute;left:134px;top:16px;font-size:10px;color:#eee;white-space:nowrap}
.footer nav{position:absolute;right:135px;top:16px;font-size:10px;color:#eee;white-space:nowrap}
.footer nav span{margin:0 9px}
</style>
</head>
<body>
<div class="hero" role="img" aria-label="Photograph of a steel arch harbour bridge under a blue sky over water"></div>

<header class="header">
  <div class="brand"><span class="brand-dot"></span><span class="brand-name">belvascotravel.com</span></div>
  <nav class="nav">
    <a class="active">HOME</a>
    <a style="left:367px">DESTINATIONS</a>
    <a style="left:473px">ACTIVITES</a>
    <a style="left:558px">TRIP STYLES</a>
    <a style="left:654px">RESPONSIBLE TRAVEL</a>
  </nav>
</header>

<section class="search">
  <div class="search-tabs"><span class="on">сторону</span><span>Класс</span></div>
  <div class="row" style="left:0;top:61px"><span class="lbl" style="width:62px">Туда</span><span class="fld" style="margin-left:18px;width:145px">Lorem Ipsum est</span></div>
  <div class="row" style="left:0;top:103px"><span class="lbl" style="width:62px">Откуда</span><span class="fld" style="margin-left:18px;width:145px">Lorem Ipsum est</span></div>
  <div class="row" style="left:0;top:146px"><span class="lbl" style="width:62px">Куда</span><span class="fld" style="margin-left:18px;width:145px">Lorem Ipsum est</span></div>
  <div class="row" style="left:230px;top:61px"><span class="lbl" style="width:44px">Туда</span><span class="fld" style="margin-left:17px;width:153px">Lorem Ipsum est</span></div>
  <div class="row" style="left:230px;top:103px"><span class="lbl" style="width:44px">Класс</span><span class="fld" style="margin-left:17px;width:153px">Lorem Ipsum est</span></div>
  <div class="row" style="left:230px;top:146px"><span class="lbl" style="width:44px">Обратно</span><span class="fld" style="margin-left:17px;width:153px">Lorem Ipsum est</span></div>
  <div class="checks"><span><i>✓</i>Обратно</span><span><i></i>В одну сторону</span></div>
  <div class="row" style="left:0;top:196px">
    <span class="lbl" style="width:82px">Пассажиры</span>
    <svg width="12" height="22" viewBox="0 0 12 22" style="margin-left:20px"><circle cx="6" cy="3" r="2.5" fill="#111"/><rect x="2" y="6" width="8" height="9" rx="2" fill="#111"/><rect x="3" y="14" width="2.4" height="8" fill="#111"/><rect x="6.6" y="14" width="2.4" height="8" fill="#111"/></svg>
    <span class="fld" style="margin-left:6px;width:73px">Enter Zip</span>
    <svg width="10" height="18" viewBox="0 0 10 18" style="margin-left:19px"><circle cx="5" cy="2.5" r="2" fill="#111"/><rect x="2" y="5" width="6" height="7" rx="1.5" fill="#111"/><rect x="2.5" y="11" width="2" height="7" fill="#111"/><rect x="5.5" y="11" width="2" height="7" fill="#111"/></svg>
    <span class="fld" style="margin-left:9px;width:73px">Enter Zip</span>
    <svg width="10" height="13" viewBox="0 0 10 13" style="margin-left:35px"><circle cx="5" cy="2.5" r="2" fill="#111"/><rect x="1.5" y="5" width="7" height="4" rx="1.5" fill="#111"/><rect x="2" y="8.5" width="2" height="4.5" fill="#111"/><rect x="6" y="8.5" width="2" height="4.5" fill="#111"/></svg>
    <span class="fld" style="margin-left:7px;width:73px">Enter Zip</span>
  </div>
  <div class="btn-check">CHECK AVAILABILITY</div>
</section>

<section class="services">
  <div class="svc" style="left:19px">
    <h3><svg width="22" height="18" viewBox="0 0 22 18"><circle cx="13" cy="2.5" r="2.3" fill="#222"/><path d="M12 5 L8 11 L3 17 M10 8 L15 11 L18 17 M11 6 L16 7 L19 4" stroke="#222" stroke-width="2.2" fill="none" stroke-linecap="round"/></svg>Visa Service</h3>
    <p>Donec sed nunc in lacus fermentum ultrices ut turpis.</p><span class="more">Read More</span>
  </div>
  <div class="svc" style="left:216px">
    <h3><svg width="28" height="12" viewBox="0 0 28 12"><path d="M1 6 L26 5 Q28 6 26 7 L14 7.5 L8 12 L6 12 L10 7.5 L3 7.5 L1 10 Z M12 5 L7 0 L9 0 L16 5 Z" fill="#222"/></svg>Flight Service</h3>
    <p>Donec sed nunc in lacus fermentum ultrices ut turpis.</p><span class="more">Read More</span>
  </div>
  <div class="svc" style="left:407px">
    <h3><svg width="24" height="16" viewBox="0 0 24 16"><rect x="0" y="0" width="2.5" height="16" fill="#222"/><rect x="0" y="8" width="24" height="4" fill="#222"/><rect x="21.5" y="5" width="2.5" height="11" fill="#222"/><rect x="3" y="4" width="5" height="4" rx="1.5" fill="#222"/><rect x="9" y="5" width="12" height="3" fill="#222"/></svg>Hotels Service</h3>
    <p>Donec sed nunc in lacus fermentum ultrices ut turpis.</p><span class="more">Read More</span>
  </div>
  <div class="svc" style="left:597px">
    <h3><svg width="28" height="12" viewBox="0 0 28 12"><path d="M1 9 L1 6 Q2 4 7 4 L10 1 L19 1 L23 4 Q27 4 27 7 L27 9 Z" fill="#222"/><circle cx="7" cy="9.5" r="2.3" fill="#fff" stroke="#222" stroke-width="1.3"/><circle cx="21" cy="9.5" r="2.3" fill="#fff" stroke="#222" stroke-width="1.3"/></svg>Rental Car Service</h3>
    <p>Donec sed nunc in lacus fermentum ultrices ut turpis.</p><span class="more">Read More</span>
  </div>
</section>

<svg class="tail" style="left:78px" width="42" height="46" viewBox="0 0 42 46"><path d="M0 0 L42 0 L42 46 L0 46 L18 23 Z" fill="var(--maroon-tail)"/></svg>
<svg class="tail" style="left:895px" width="42" height="46" viewBox="0 0 42 46"><path d="M0 0 L42 0 L24 23 L42 46 L0 46 Z" fill="var(--maroon-tail)"/></svg>
<section class="banner">
  <svg class="slash" width="16" height="16" viewBox="0 0 16 16"><path d="M2 2 L14 14" stroke="#fff" stroke-width="2.4" stroke-linecap="round"/></svg>
  <h2>Lorem Ipsum est simplement</h2>
  <p>Lorem Ipsum est simplement du faux texte employé dans la sition et la misen page avant impression.</p>
  <div class="btn-contact">Contact Us Now</div>
</section>

<main class="content">
  <div class="tabs">
    <span class="on">VISA SERVICE</span>
    <span style="left:188px">Flight Service</span>
    <span style="left:335px">Hotels Service</span>
    <span style="left:496px">Other Services</span>
    <span class="phone">YOU CALL, WE'RE THERE<br>(866-BVTRIPS)</span>
  </div>
  <p class="intro">Lorem ipsum dolor sit amet, consectetuer adipiscing elit, sed diam nonummy nibh euismod tincidunt ut laoreet dolore magna aliquam erat volutpat. Ut wisi enim ad minim veniam, quis nostrud exerci tation ullamcorper suscipit lobortis nisl ut aliquip ex ea commodo consequat. Duis autem vel eum iriure dolor in hendrerit in vulputate velit esse molestie consequat, vel illum dolore eu feugiat nulla facilisis at vero eros et accumsan et iusto odio dignissim qui blandit praesent lupta-tum zzril delenit augue duis dolore te feugait nulla facilisi. Nam liber tempor cum soluta nobis eleifend option congue nihil imperdiet doming id quod mazim placerat facer possim assum.</p>

  <div class="col" style="left:17px">
  <h4><svg width="31" height="31" viewBox="0 0 31 31"><circle cx="15.5" cy="15.5" r="13.5" fill="none" stroke="var(--lime)" stroke-width="3"/><path d="M8 15.5 H19 M15 10 L21 15.5 L15 21" stroke="var(--lime)" stroke-width="3.5" fill="none"/></svg>Lorem Ipsum est simplement</h4>
    <ul>
      <li>Lorem Ipsum est simplement du faux texte employé dans la sition et la misen page avant impression.</li>
      <li>Lorem Ipsum est simplement du faux texte employé dans la sition et la misen page avant impression.</li>
      <li>Lorem Ipsum est simplement du faux texte employé dans la sition et la misen page avant impression.</li>
      <li>Lorem Ipsum est simplement du faux texte employé dans la sition et la misen page avant impression.</li>
    </ul>
  </div>
  <div class="col" style="left:406px">
  <h4><svg width="31" height="31" viewBox="0 0 31 31"><circle cx="15.5" cy="15.5" r="13.5" fill="none" stroke="var(--lime)" stroke-width="3"/><path d="M8 15.5 H19 M15 10 L21 15.5 L15 21" stroke="var(--lime)" stroke-width="3.5" fill="none"/></svg>Lorem Ipsum est simplement</h4>
    <ul>
      <li>Lorem Ipsum est simplement du faux texte employé dans la sition et la misen page avant impression.</li>
      <li>Lorem Ipsum est simplement du faux texte employé dans la sition et la misen page avant impression.</li>
      <li>Lorem Ipsum est simplement du faux texte employé dans la sition et la misen page avant impression.</li>
      <li>Lorem Ipsum est simplement du faux texte employé dans la sition et la misen page avant impression.</li>
    </ul>
  </div>
  <a class="more-link">More Servies</a>
</main>

<footer class="footer">
  <div class="copy">Copyright 2013 BelvascoTravel. All Rights Reserved.</div>
  <nav>Home<span>|</span>Destinations<span>|</span>Activites<span>|</span>Trip Styles<span>|</span>Responsible Travel</nav>
</footer>
</body>
</html>
```